Copperleaf Roofing Business Card

This is my current business card. But I’d like to make some changes. Somewhere on the card I’d like to list some of the services we offer. Maybe on the back? But I’d still like to keep the red. White and black modern look.

-residential & commercial roofing
-Roof Repairs & Maintenance
-Storm Damage & Insurance Claims specialist
-Christmas Lights and permanent Christmas lights
Fencing. Windows. Gutters. Siding. Sheetrock, painting.

```html
<!DOCTYPE html>
<html lang="en">
<head>
<meta charset="UTF-8">
<title>Copperleaf Roofing Business Card</title>
<link href="https://fonts.googleapis.com/css2?family=Montserrat:wght@400;500;700;800&family=Michroma&display=swap" rel="stylesheet">
<style>
  :root {
    --page-bg: #d4d5d7;
    --red: #e0212a;
    --deep-red: #6b0f12;
    --black: #111111;
    --white: #ffffff;
    --text: #1b1b1b;
  }
  * { margin: 0; padding: 0; box-sizing: border-box; }
  html, body { width: 900px; height: 1200px; overflow: hidden; }
  body {
    background: var(--page-bg);
    font-family: "Montserrat", sans-serif;
    color: var(--text);
    position: relative;
  }
  .card {
    position: absolute;
    left: 121px;
    width: 658px;
    border-radius: 14px;
    overflow: hidden;
  }
  .card-front { top: 204px; height: 375px; }
  .card-back { top: 619px; height: 382px; background: var(--white); }

  .tartan-field {
    position: absolute; inset: 0;
    background: linear-gradient(180deg,
      var(--deep-red) 0%, var(--red) 22%, #f2d6d6 30%, var(--red) 38%,
      var(--black) 52%, var(--black) 64%, var(--red) 70%, var(--deep-red) 80%);
  }
  .brand-mark {
    position: absolute; left: 50%; transform: translateX(-50%);
    width: 150px; height: 150px; border-radius: 50%;
  }
  .card-front .brand-mark { top: 74px; background: var(--black); }
  .card-back .brand-mark { top: 18px; width: 118px; height: 118px; background: var(--red); }

  .brand-name {
    position: absolute; left: 0; right: 0; text-align: center;
    font-family: "Montserrat", sans-serif; font-weight: 800;
    line-height: 1; letter-spacing: 1px;
  }
  .brand-name .line-1 { display: block; }
  .brand-name .line-2 { display: block; margin-top: 8px; }
  .card-front .brand-name { top: 240px; color: var(--white); }
  .card-front .line-1 { font-size: 38px; }
  .card-front .line-2 { font-size: 25px; }
  .card-back .brand-name { top: 146px; color: var(--red); }
  .card-back .line-1 { font-size: 30px; }
  .card-back .line-2 { font-size: 20px; margin-top: 6px; }

  .services {
    position: absolute; right: 352px; top: 232px;
    list-style: none; text-align: right;
    font-size: 14px; line-height: 17px;
  }
  .services li { position: relative; padding-right: 12px; margin-bottom: 6px; }
  .services li::after {
    content: ""; position: absolute; right: 0; top: 50%;
    width: 5px; height: 5px; border-radius: 50%; background: var(--red);
    transform: translateY(-50%);
  }
  .divider {
    position: absolute; left: 325px; top: 228px;
    width: 2px; height: 126px; background: var(--red);
  }
  .contact { position: absolute; left: 342px; top: 230px; }
  .person-name {
    font-family: "Michroma", sans-serif; font-size: 21px;
    letter-spacing: 1px; color: var(--black); line-height: 1.1;
  }
  .person-name .surname { color: var(--red); }
  .person-role { font-size: 14px; margin-top: 4px; }
  .contact-list { list-style: none; margin-top: 8px; font-size: 14px; }
  .contact-list li { display: flex; align-items: center; height: 24px; }
  .contact-list svg { width: 12px; height: 12px; margin-right: 9px; fill: var(--red); }
</style>
</head>
<body>

<section class="card card-front">
  <div class="tartan-field" role="img" aria-label="Red, black and white tartan pattern background"></div>
  <div class="brand-mark"></div>
  <h1 class="brand-name"><span class="line-1">COPPERLEAF</span><span class="line-2">ROOFING CO.</span></h1>
</section>

<section class="card card-back">
  <div class="brand-mark"></div>
  <h2 class="brand-name"><span class="line-1">COPPERLEAF</span><span class="line-2">ROOFING CO.</span></h2>

  <ul class="services">
    <li>residential &amp; commercial roofing</li>
    <li>Roof Repairs &amp; Maintenance</li>
    <li>Storm Damage &amp;<br>Insurance Claims specialist</li>
    <li>Fencing. Windows. Gutters.<br>Siding. Sheetrock, painting</li>
  </ul>

  <div class="divider"></div>

  <div class="contact">
    <p class="person-name">DALE <span class="surname">MERCER</span></p>
    <p class="person-role">Owner</p>
    <ul class="contact-list">
      <li><svg viewBox="0 0 24 24"><path d="M6.6 10.8a15 15 0 0 0 6.6 6.6l2.2-2.2a1 1 0 0 1 1-.25 11.4 11.4 0 0 0 3.6.57 1 1 0 0 1 1 1V20a1 1 0 0 1-1 1A17 17 0 0 1 3 4a1 1 0 0 1 1-1h3.5a1 1 0 0 1 1 1c0 1.25.2 2.45.57 3.57a1 1 0 0 1-.25 1z"/></svg>555-013-2849</li>
      <li><svg viewBox="0 0 24 24"><path d="M2 5h20v2l-10 6L2 7zm0 4l10 6 10-6v10H2z"/></svg>dale@copperleafroofing.com</li>
      <li><svg viewBox="0 0 24 24"><path d="M12 2a10 10 0 1 0 0 20 10 10 0 0 0 0-20zm-1 17.9A8 8 0 0 1 4.2 10l4.8 4.8v1a2 2 0 0 0 2 2zm6.9-2.5A2 2 0 0 0 16 16h-1v-3a1 1 0 0 0-1-1H8v-2h2a1 1 0 0 0 1-1V7h2a2 2 0 0 0 2-2v-.4a8 8 0 0 1 2.9 12.8z"/></svg>www.copperleafroofing.com</li>
    </ul>
  </div>
</section>

</body>
</html>
```